Business Card Design: recruitment/consultancy for business Thrive360onward

We need a business card design for a new company based in Adelaide Australia called Thrive360onward. Our Business aims to support people over 50 who may be looking for a career change, have been made redundant or generally looking for employment. We will also be working with businesses to provide them with recruiting solutions, job design, recruitment strategies and customised training. we will also be working with volunteering opportunities for those over 50.
We would like to see the E in thrive360onward strong and dominant. The final design should reflect change for the better, better opportunities, today is the day, make way for the new, all aimed at the 50 plus age group.
Colours we are thinking off include green (money, growth) black and white.... we like the idea of black and white photography with a one dominant colour...think of a of a black and white photo of a woman with dominant red lips...that sort of look

Business

Contact Information for Business Card

Kim, Mavis & Gwen
phone: 0439615028
Thrive360onward@mailbox-example.net
Facebook/Thrive360onward
www.thrive360onward-example.com.au

```html
<!DOCTYPE html>
<html lang="en">
<head>
<meta charset="utf-8">
<title>Thrive360onward – Business Card</title>
<link rel="stylesheet" href="https://fonts.googleapis.com/css2?family=Gentium+Book+Plus:ital,wght@0,400;1,400;1,700&display=swap">
<style>
  :root {
    --page-bg: #d9dbd6;
    --card-top: #6a6b69;
    --card-mid: #7d8376;
    --card-low: #98a08d;
    --ink-light: #ffffff;
    --ink-dark: #141414;
    --accent-red: #c8141c;
    --band: #a9a9ab;
    --photo-dark: #262626;
    --photo-mid: #7a7a7a;
    --photo-light: #d6d6d6;
  }
  html, body {
    margin: 0;
    padding: 0;
    width: 1200px;
    height: 902px;
    overflow: hidden;
    background: var(--page-bg);
  }
  .canvas {
    position: relative;
    width: 1200px;
    height: 902px;
  }
  .business-card {
    position: absolute;
    left: 100px;
    top: 165px;
    width: 1000px;
    height: 571px;
    border-radius: 24px;
    overflow: hidden;
    background: linear-gradient(165deg, var(--card-top) 0%, var(--card-mid) 55%, var(--card-low) 100%);
    font-family: "Gentium Book Plus", Georgia, serif;
  }
  .brand {
    position: absolute;
    left: 48px;
    top: 68px;
    display: flex;
    align-items: center;
    gap: 16px;
  }
  .brand-name {
    margin: 0;
    font-size: 62px;
    font-weight: 400;
    line-height: 1;
    color: var(--ink-light);
  }
  .brand-dot {
    width: 18px;
    height: 18px;
    border-radius: 50%;
    background: var(--accent-red);
    margin-top: 14px;
  }
  .contact-list {
    position: absolute;
    left: 30px;
    width: 504px;
    top: 218px;
    margin: 0;
    padding: 0;
    list-style: none;
    text-align: center;
    font-style: italic;
    font-size: 28px;
    line-height: 40px;
    color: var(--ink-light);
  }
  .team-band {
    position: absolute;
    left: 0;
    top: 454px;
    width: 645px;
    height: 117px;
    background: var(--band);
  }
  .team-names {
    position: absolute;
    left: 0;
    width: 600px;
    top: 484px;
    margin: 0;
    text-align: center;
    font-style: italic;
    font-weight: 700;
    font-size: 50px;
    line-height: 1;
    color: var(--ink-dark);
  }
  .portrait {
    position: absolute;
    right: 0;
    top: 0;
    width: 432px;
    height: 571px;
    background: linear-gradient(100deg, var(--photo-dark) 0%, var(--photo-mid) 35%, var(--photo-light) 60%, var(--photo-mid) 80%, var(--photo-dark) 100%);
  }
</style>
</head>
<body>
<main class="canvas">
  <section class="business-card">
    <div class="brand">
      <h1 class="brand-name">thrive360onward</h1>
      <span class="brand-dot"></span>
    </div>
    <ul class="contact-list">
      <li>0439615028</li>
      <li>Thrive360onward@mailbox-example.net</li>
      <li>Facebook/Thrive360onward</li>
      <li>www.thrive360onward-example.com.au</li>
    </ul>
    <div class="team-band"></div>
    <p class="team-names">Kim, Mavis &amp; Gwen</p>
    <div class="portrait" role="img" aria-label="Black and white portrait photograph of a smiling woman with curled hair and bright red lips"></div>
  </section>
</main>
</body>
</html>
```